Animal Eye Clinic needs a Business card

We are a new veterinary ophthalmology practice (Ridgeline Pet Vision Care) and we need a business card designed. We only see animal eyes - we are not a regular veterinary clinic. We already have a logo. We are looking for a professional, good looking business card to hand out to our clients. We are looking for something simple but professional and contemporary. Our logo is likely the only picture/graphic that needs to be on the card.
Updates

Contact Information for Business Card

Delia Vossman, BSc, DVM, MSc, DipACVO
Veterinary Ophthalmologist

Phone: 250.418.3927
Email: ridgelinepetvisioncare@mailbox-example.net
Website: ridgelinepetvisioncare-example.net
Address: 1874 Thornbury Rd
Kelowna, BC, V1X 4M9

Colors

Designer to choose colors to be used in the design.

Requirements
Must have
• Our logo (attached)

```html
<!DOCTYPE html>
<html lang="en">
<head>
<meta charset="utf-8">
<title>Ridgeline Pet Vision Care – Business Card</title>
<link rel="stylesheet" href="https://fonts.googleapis.com/css2?family=Lato:wght@400;700&family=Tinos&display=swap">
<style>
  :root {
    --backdrop: #2b2b2b;
    --teal: #2a9fb0;
    --teal-deep: #1f8494;
    --slate: #565656;
    --ink-light: #ececec;
    --ink-muted: #d6d6d6;
  }
  * { margin: 0; padding: 0; box-sizing: border-box; }
  html, body {
    width: 1200px; height: 1200px; overflow: hidden;
    background: var(--backdrop);
    font-family: "Lato", sans-serif;
  }
  .canvas {
    width: 1200px; height: 1200px;
    display: flex; flex-direction: column;
    align-items: center; justify-content: center; gap: 50px;
  }
  .card {
    width: 900px; height: 515px; position: relative;
    box-shadow: 0 6px 18px rgba(0,0,0,.35);
  }
  .card-front {
    background: var(--teal);
    display: flex; align-items: center; justify-content: center;
  }
  .brand { display: flex; align-items: center; gap: 24px; }
  .brand-dot {
    width: 96px; height: 96px; border-radius: 50%;
    background: var(--ink-light);
  }
  .brand-name {
    color: var(--ink-light); font-weight: 700;
    font-size: 40px; letter-spacing: 1px;
  }
  .card-back {
    background: var(--slate); color: var(--ink-light);
    padding: 78px 52px 0 52px;
  }
  .role {
    font-size: 31px; letter-spacing: 5px; font-weight: 400;
  }
  .identity { display: flex; align-items: baseline; gap: 22px; margin-top: 14px; }
  .person-name {
    font-family: "Tinos", serif; font-size: 64px;
    color: var(--teal-deep);
  }
  .credentials { font-size: 20px; letter-spacing: 3.5px; color: var(--ink-light); }
  .contact {
    position: absolute; left: 52px; top: 330px;
    display: grid; grid-template-columns: 80px auto; row-gap: 6px;
    font-size: 22px; letter-spacing: 1.6px; color: var(--ink-muted);
  }
  .contact .addr { margin-top: 18px; }
  .corner-brand {
    position: absolute; right: 48px; bottom: 52px;
    display: flex; flex-direction: column; align-items: center; gap: 10px;
  }
  .corner-dot {
    width: 90px; height: 90px; border-radius: 50%;
    background: var(--ink-light);
  }
  .corner-name { font-size: 13px; font-weight: 700; color: var(--ink-light); letter-spacing: .5px; }
</style>
</head>
<body>
<main class="canvas">
  <section class="card card-front" aria-label="Card front">
    <div class="brand">
      <span class="brand-dot" aria-hidden="true"></span>
      <span class="brand-name">Ridgeline Pet Vision Care</span>
    </div>
  </section>

  <section class="card card-back" aria-label="Card back">
    <p class="role">Veterinary Ophthalmologist</p>
    <div class="identity">
      <h1 class="person-name">Delia Vossman</h1>
      <span class="credentials">BSc, DVM, MSc, DipACVO</span>
    </div>
    <div class="contact">
      <span>P:</span><span>250.418.3927</span>
      <span>E:</span><span>ridgelinepetvisioncare@mailbox-example.net</span>
      <span>W:</span><span>ridgelinepetvisioncare-example.net</span>
      <span class="addr">Add:</span><span class="addr">1874 Thornbury Rd Kelowna, BC, V1X 4M9</span>
    </div>
    <div class="corner-brand">
      <span class="corner-dot" aria-hidden="true"></span>
      <span class="corner-name">Ridgeline Pet Vision Care</span>
    </div>
  </section>
</main>
</body>
</html>
```